Whitcombe Business Card Design

The name of the business is Dario Whitcombe, CPA LLC
The service that we offer is Accounting, Tax & Consulting Services. I need it to have the following items:
Dario Whitcombe, Principal
Phone Number
Email Address
Physical Address

I have attached the company logo, one in black and one in white. Please provide a design in black background and the other in white background. Please include "Accounting, Tax & Consulting Services". I want the business card to be clean and very professional.

```html
<!DOCTYPE html>
<html lang="en">
<head>
<meta charset="UTF-8">
<title>Dario Whitcombe, CPA LLC – Business Card</title>
<link href="https://fonts.googleapis.com/css2?family=Montserrat:wght@500;600&family=Roboto:wght@300&display=swap" rel="stylesheet">
<style>
  :root {
    --backdrop: #2c2c2c;
    --card-top: #232325;
    --card-bottom: #2b2b2d;
    --brand-red: #8d1b1c;
    --text-white: #f2f2f2;
    --text-soft: #d6d6d6;
    --text-grey: #a3a3a3;
    --mark-grey: #7d7d80;
  }
  * { margin: 0; padding: 0; box-sizing: border-box; }
  html, body { width: 1200px; height: 1138px; overflow: hidden; background: var(--backdrop); }
  .canvas { position: relative; width: 1200px; height: 1138px; }

  .card {
    position: absolute;
    border-radius: 16px;
    overflow: hidden;
    background: linear-gradient(160deg, var(--card-top), var(--card-bottom));
  }
  .card--front { left: 272px; top: 184px; width: 622px; height: 376px; }
  .card--back  { left: 274px; top: 606px; width: 619px; height: 375px; }

  .front-name {
    position: absolute; inset: 0;
    display: flex; align-items: center; justify-content: center;
    font-family: "Montserrat", sans-serif; font-weight: 600;
    font-size: 28px; letter-spacing: 1px; color: var(--mark-grey);
    text-transform: uppercase;
  }

  .firm-name {
    position: absolute; left: 27px; top: 54px;
    font-family: "Montserrat", sans-serif; font-weight: 600;
    font-size: 23px; color: var(--text-white); text-transform: uppercase;
    white-space: nowrap;
  }
  .firm-tagline {
    position: absolute; left: 27px; top: 84px;
    font-family: "Montserrat", sans-serif; font-weight: 500;
    font-size: 15.5px; letter-spacing: 2.2px; color: var(--text-grey);
    white-space: nowrap;
  }
  .person-name {
    position: absolute; left: 27px; top: 156px;
    font-family: "Montserrat", sans-serif; font-weight: 600;
    font-size: 21px; color: var(--brand-red); text-transform: uppercase;
  }
  .person-role {
    position: absolute; left: 27px; top: 182px;
    font-family: "Roboto", sans-serif; font-weight: 300;
    font-size: 17px; color: var(--text-soft);
  }
  .contact-list { position: absolute; left: 27px; top: 224px; list-style: none; }
  .contact-item {
    display: flex; align-items: center; gap: 10px; height: 24px;
    font-family: "Roboto", sans-serif; font-weight: 300;
    font-size: 16.5px; color: var(--text-soft);
  }
  .contact-icon { width: 14px; height: 14px; flex: none; }
  .address {
    position: absolute; left: 27px; top: 304px;
    font-family: "Roboto", sans-serif; font-weight: 300;
    font-size: 16.5px; line-height: 24px; color: var(--text-soft);
  }
  .service-band { position: absolute; left: 248px; bottom: 0; width: 371px; height: 45px; }
  .service-text {
    position: absolute; right: 35px; bottom: 13px;
    font-family: "Roboto", sans-serif; font-weight: 300;
    font-size: 16.5px; color: var(--text-white);
  }
</style>
</head>
<body>
<div class="canvas">
  <section class="card card--front">
    <div class="front-name">Dario Whitcombe, CPA LLC</div>
  </section>

  <section class="card card--back">
    <h1 class="firm-name">Dario Whitcombe, CPA, LLC</h1>
    <p class="firm-tagline">CERTIFIED PUBLIC ACCOUNTANT</p>

    <h2 class="person-name">Dario Whitcombe</h2>
    <p class="person-role">Principal</p>

    <ul class="contact-list">
      <li class="contact-item">
        <svg class="contact-icon" viewBox="0 0 14 14"><path fill="#8d1b1c" d="M1 5c0-2 3-3 6-3s6 1 6 3v1h-3V4.5H4V6H1zM3 7h8l1 5H2z"/></svg>
        704-555-0186
      </li>
      <li class="contact-item">
        <svg class="contact-icon" viewBox="0 0 14 14"><rect x="1" y="3" width="12" height="8" fill="#8d1b1c"/><path d="M1 3l6 5 6-5" stroke="#2a2a2c" stroke-width="1.2" fill="none"/></svg>
        dw@whitcombecpa.com
      </li>
      <li class="contact-item">
        <svg class="contact-icon" viewBox="0 0 14 14"><circle cx="7" cy="7" r="5.5" fill="none" stroke="#8d1b1c" stroke-width="1.3"/><ellipse cx="7" cy="7" rx="2.3" ry="5.5" fill="none" stroke="#8d1b1c" stroke-width="1.1"/><path d="M1.5 7h11" stroke="#8d1b1c" stroke-width="1.1"/></svg>
        www.whitcombecpa.com
      </li>
    </ul>

    <address class="address" style="font-style: normal;">
      418, Larkfield Avenue, Suite 2<br>Brookhaven, US 28207
    </address>

    <svg class="service-band" viewBox="0 0 371 45" preserveAspectRatio="none">
      <path d="M30 0H371V45H0Z" fill="#8d1b1c"/>
    </svg>
    <p class="service-text">Accounting, Tax &amp; Consulting Services</p>
  </section>
</div>
</body>
</html>
```